Classy, Elegant, Simple Business Card Design

Looking to have a classy, simple, and elegant design. Want a top notch designed business card. I really like the look of the new torvane credit card. I also like the design I attached. I am trying to reach 21-29 year old females for booking us for there wedding or event. We offer Disc Jockey Service, Photo Booth Rentals, and Uplighting .

Target Market(s)

21-28 year old females

Contact Information for Business Card

Has to have logo, website, email, and phone number

Font styles to use
Other font styles liked:
• open to font choice, modern, clean
Designer to choose
33a6d7
0791cd
0555a3
ffffff

Requirements
Must have
• Has to have logo, website, email, and phone number
Nice to have
• I really like the design of the new torvane credit card. I also included my logo and some designs I like
Should not have
• clutter or too much info

```html
<!DOCTYPE html>
<html lang="en">
<head>
<meta charset="utf-8">
<title>Tidelight Event Group – Business Card</title>
<link href="https://fonts.googleapis.com/css2?family=Jost:wght@400;500&display=swap" rel="stylesheet">
<style>
  :root {
    --backdrop: #3f3f3f;
    --card: #242424;
    --brand-silver: #b9b9b9;
    --text-light: #ffffff;
  }
  html, body {
    margin: 0;
    padding: 0;
    width: 1200px;
    height: 900px;
    overflow: hidden;
    background: var(--backdrop);
    font-family: "Jost", sans-serif;
  }
  .canvas {
    position: relative;
    width: 1200px;
    height: 900px;
  }
  .card {
    position: absolute;
    left: 297px;
    width: 608px;
    height: 348px;
    border-radius: 20px;
    background: var(--card);
  }
  .card--front { top: 84px; }
  .card--back { top: 468px; }

  .brand-wordmark {
    position: absolute;
    left: 0;
    right: 0;
    top: 136px;
    text-align: center;
    color: var(--brand-silver);
    font-weight: 400;
    line-height: 1;
  }
  .brand-wordmark__name {
    display: block;
    font-size: 42px;
    letter-spacing: 1px;
  }
  .brand-wordmark__tagline {
    display: block;
    margin-top: 6px;
    font-size: 19px;
    letter-spacing: 8px;
    padding-left: 8px;
  }

  .brand-mark {
    position: absolute;
    left: 50px;
    top: 150px;
    display: flex;
    align-items: center;
    gap: 12px;
    color: var(--brand-silver);
    font-weight: 400;
    font-size: 26px;
    letter-spacing: 2px;
  }
  .brand-mark__dot {
    width: 14px;
    height: 14px;
    border-radius: 50%;
    background: var(--brand-silver);
  }

  .contact {
    position: absolute;
    left: 307px;
    top: 116px;
    color: var(--text-light);
  }
  .contact__name {
    margin: 0 0 14px;
    font-size: 21px;
    font-weight: 500;
    letter-spacing: 0.5px;
  }
  .contact__line {
    margin: 0;
    font-size: 16px;
    line-height: 25px;
    font-weight: 400;
    letter-spacing: 0.3px;
  }
</style>
</head>
<body>
  <main class="canvas">
    <section class="card card--front" aria-label="Card front">
      <div class="brand-wordmark">
        <span class="brand-wordmark__name">TIDELIGHT</span>
        <span class="brand-wordmark__tagline">EVENT GROUP</span>
      </div>
    </section>

    <section class="card card--back" aria-label="Card back">
      <div class="brand-mark">
        <span class="brand-mark__dot"></span>
        <span class="brand-mark__name">TIDELIGHT</span>
      </div>
      <div class="contact">
        <p class="contact__name">Daniel R. Hale</p>
        <p class="contact__line">555 014 2290</p>
        <p class="contact__line">hello@tidelighteventgroup.com</p>
        <p class="contact__line">www.tidelighteventgroup.com</p>
      </div>
    </section>
  </main>
</body>
</html>
```